Cover for a Non-Fiction Book on Authoritarianism for a Washington D.C. Think Tank

Create a dynamic and engaging cover highlighting the role of contemporary and historical authoritarianism for a non-fiction edited volume. The book brings together chapters from many leading academics on the subject. The tone should be serious but provocative. Proprietary images are not acceptable as we are not budgeting for licensing. The books dimensions are 6x9. Preference will be given to designers with front and back cover design with sample ipsum lorum text.

One of covers that we particularly liked was "When Quiet Crowds Prevail" a link to the image on shelvora is: http://www.shelvora.example/s/ref=nb_sb_noss/190-2603447-3311705?url=search-alias%3Daps&field-keywords=When+Quiet+Crowds+Prevail

Attached is a draft version of the manuscript to assist in shaping your creative vision.

Project Deadline Extended Reason: I have extended the deadline at the request of the editors. They would like to see some designs that rely less heavily on the themes of fists and barbed wire to reference authoritarianism. I apologize to designs with current submissions, some of them are very professional, however none of the designs are currently under consideration for use. Added Saturday, January 24, 2015

Project Deadline Extended Reason: Editors are still unsatisfied with current sample of options. I apologize to those current contributors, but anything challenging and new would be well received. Added Friday, January 30, 2015

Project Deadline Extended Reason: I've updated the deadline so that designers that were well ranked can submit full front and back covers to assist the book editors in making their final decision. Added Friday, February 13, 2015

Font styles to use
Serif
Sans Serif

Requirements
Must have
• 1) Title: Are Strongmen Quietly Returning Again
• 2) Editors: Dorian Kettleby and Lucia R. Venhorst
• 3) Language from client: "a simple design that captured both a symbol of repression and resistance would be ideal. The cover of When Quiet Crowds Prevail is a great example. Nothing busy or overly complicated. The image of mass street protests may be overused at this point so I'd opt for something a bit more creative. Vibrant colors always great."
• 4) This final project design must use the attached InDesign template file when constructing the cover (IDML and INDD versions of the template are available).
Nice to have
• Feel free to use Meridale Forum logo designs pulled from the web.
Should not have
• Photographs that would require compensating a copyright holder.

```html
<!DOCTYPE html>
<html lang="en">
<head>
<meta charset="utf-8">
<title>Are Strongmen Quietly Returning Again? — Book Cover</title>
<link rel="stylesheet" href="https://fonts.googleapis.com/css2?family=Montserrat:wght@700;800&family=Open+Sans:wght@300&display=swap">
<style>
  :root {
    --teal: #00c2c7;
    --ink: #000000;
    --paper: #ffffff;
    --steel-mid: #6e6e6e;
    --steel-dark: #262626;
  }
  html, body {
    margin: 0;
    padding: 0;
    overflow: hidden;
    background: var(--paper);
  }
  .cover {
    position: relative;
    width: 796px;
    height: 1200px;
    background: var(--teal);
    overflow: hidden;
  }
  .editors {
    position: absolute;
    top: 60px;
    left: 0;
    width: 100%;
    text-align: center;
    font-family: "Open Sans", sans-serif;
    font-weight: 300;
    font-size: 31px;
    line-height: 1;
    color: var(--paper);
    margin: 0;
  }
  .emblem {
    position: absolute;
    top: 0;
    left: 0;
    width: 796px;
    height: 820px;
  }
  .title {
    margin: 0;
    font-family: "Montserrat", sans-serif;
    font-weight: 800;
    text-transform: uppercase;
  }
  .title-line {
    position: absolute;
    display: flex;
    align-items: center;
    justify-content: center;
    box-sizing: border-box;
    white-space: nowrap;
  }
  .title-line--lead {
    left: 48px;
    top: 826px;
    width: 718px;
    height: 94px;
    background: var(--ink);
    color: var(--paper);
    font-size: 72px;
    transform: rotate(-2.4deg);
  }
  .title-line--middle {
    left: 30px;
    top: 932px;
    width: 736px;
    height: 76px;
    color: var(--ink);
    font-size: 58px;
  }
  .title-line--close {
    left: 42px;
    top: 1014px;
    width: 734px;
    height: 94px;
    background: var(--ink);
    color: var(--paper);
    font-size: 58px;
    transform: rotate(-3deg);
  }
  .publisher {
    position: absolute;
    left: 0;
    bottom: 36px;
    width: 100%;
    display: flex;
    align-items: center;
    justify-content: center;
    gap: 8px;
    font-family: "Montserrat", sans-serif;
    font-weight: 700;
    font-size: 25px;
    line-height: 1;
    color: var(--paper);
  }
  .publisher-mark {
    width: 22px;
    height: 22px;
    border-radius: 50%;
    background: var(--paper);
  }
</style>
</head>
<body>
  <main class="cover">
    <p class="editors">Dorian Kettleby and Lucia R. Venhorst</p>

    <svg class="emblem" viewBox="0 0 796 820">
      <defs>
        <radialGradient id="boot-tone" cx="0.5" cy="0.5" r="0.5">
          <stop offset="0" stop-color="var(--steel-mid)"/>
          <stop offset="0.6" stop-color="var(--steel-dark)" stop-opacity="0.9"/>
          <stop offset="1" stop-color="var(--steel-dark)" stop-opacity="0"/>
        </radialGradient>
      </defs>
      <circle class="emblem-disc" cx="485" cy="470" r="287" fill="var(--ink)"/>
      <ellipse role="img" aria-label="Illustration of a heavy laced combat boot stepping onto a raised clenched fist"
               cx="330" cy="510" rx="320" ry="270" fill="url(#boot-tone)"/>
    </svg>

    <h1 class="title">
      <span class="title-line title-line--lead">Are</span>
      <span class="title-line title-line--middle">Strongmen Quietly</span>
      <span class="title-line title-line--close">Returning Again?</span>
    </h1>

    <div class="publisher">
      <span class="publisher-mark"></span>
      <span class="publisher-name">Meridale Forum</span>
    </div>
  </main>
</body>
</html>
```